Design a compelling Tarnwove Business Card that will drive people to my site

I want a business card that I can give to people—less to tell them who I am and more to direct them to my website. My website is a portal for Pelmor Aquatics Officials and a place for people who want to become Pelmor Aquatics Officials.
I am uploading my official company logo as well as a business card mockup that I did on my own. Please feel free to completely stray from this design.
I've included a screen recording of the homepage of my website as well.
Target Market(s)
Pelmor Aquatics Officials and people who desire to become one
Contact Information for Business Card
website url
Look and feel
Each slider illustrates characteristics of the customer's brand and the style your logo design should communicate.

```html
<!DOCTYPE html>
<html lang="en">
<head>
<meta charset="utf-8">
<title>Tarnwove Business Card</title>
<link rel="stylesheet" href="https://fonts.googleapis.com/css2?family=Montserrat:wght@400;500;600;700&display=swap">
<style>
  :root {
    --brand-blue: #3a55a8;
    --soft-blue: #9aaedb;
    --card-white: #ffffff;
    --stage: #e9ebf0;
    --shadow: rgba(20, 30, 60, 0.18);
  }
  * { box-sizing: border-box; margin: 0; padding: 0; }
  html, body { width: 1200px; height: 912px; overflow: hidden; }
  body {
    background: var(--stage);
    font-family: "Montserrat", sans-serif;
    position: relative;
  }
  .card {
    position: absolute;
    top: 296px;
    width: 560px;
    height: 320px;
    border-radius: 18px;
    overflow: hidden;
    box-shadow: 0 8px 24px var(--shadow);
  }
  .card--front { left: 20px; background: var(--brand-blue); }
  .card--back { left: 620px; background: var(--card-white); }

  .front__wordmark {
    position: absolute;
    left: 0; right: 0; top: 112px;
    text-align: center;
    color: var(--card-white);
    font-weight: 600;
    font-size: 64px;
    letter-spacing: -1px;
    line-height: 1;
  }
  .front__tagline {
    position: absolute;
    left: 0; right: 0; top: 214px;
    text-align: center;
    color: var(--card-white);
    font-weight: 400;
    font-size: 15px;
    letter-spacing: 0.3px;
  }

  .back__shapes { position: absolute; inset: 0; }
  .back__wordmark {
    position: absolute;
    left: 36px; top: 116px;
    color: var(--brand-blue);
    font-weight: 600;
    font-size: 56px;
    letter-spacing: -1px;
    line-height: 1;
  }
  .back__person {
    position: absolute;
    left: 336px; top: 118px;
    width: 192px;
    text-align: center;
  }
  .back__name {
    color: var(--brand-blue);
    font-weight: 700;
    font-size: 19px;
    white-space: nowrap;
  }
  .back__role {
    color: var(--card-white);
    font-weight: 500;
    font-size: 13px;
    margin-top: 4px;
  }
  .back__contacts {
    position: absolute;
    left: 44px; top: 222px;
    list-style: none;
  }
  .back__contact {
    display: flex;
    align-items: center;
    gap: 10px;
    color: var(--card-white);
    font-size: 16px;
    font-weight: 500;
    height: 28px;
  }
  .back__icon { width: 16px; height: 16px; flex: none; }
</style>
</head>
<body>

  <section class="card card--front" role="img" aria-label="Front of card: brand blue field with faint repeating brand pattern">
    <div class="front__wordmark">tarnwove</div>
    <p class="front__tagline">Your Poolside Referee Network</p>
  </section>

  <section class="card card--back">
    <svg class="back__shapes" width="560" height="320" viewBox="0 0 560 320" aria-hidden="true">
      <rect x="0" y="196" width="560" height="124" fill="var(--brand-blue)"/>
      <rect x="322" y="100" width="238" height="100" fill="var(--brand-blue)"/>
      <polyline points="0,190 318,190 318,96 560,96" fill="none" stroke="var(--soft-blue)" stroke-width="5"/>
      <path d="M336 100 H528 V176 Q528 192 512 192 H352 Q336 192 336 176 Z"
            fill="var(--soft-blue)" stroke="var(--card-white)" stroke-width="3"/>
    </svg>

    <div class="back__wordmark">tarnwove</div>

    <div class="back__person">
      <p class="back__name">Daniel Varesco</p>
      <p class="back__role">CEO &amp; Founder</p>
    </div>

    <ul class="back__contacts">
      <li class="back__contact">
        <svg class="back__icon" viewBox="0 0 16 16" aria-hidden="true">
          <path d="M4 1.5 L6 4.5 L4.8 6 Q6 9 9.8 11.2 L11.3 10 L14.5 12 L13 14.5 Q7 15 3 9 Q1 5.5 1.8 3 Z" fill="var(--soft-blue)"/>
        </svg>
        (555) 019-2847
      </li>
      <li class="back__contact">
        <svg class="back__icon" viewBox="0 0 16 16" aria-hidden="true">
          <rect x="1" y="3" width="14" height="10" rx="1" fill="var(--soft-blue)"/>
          <polyline points="1.5,3.5 8,9 14.5,3.5" fill="none" stroke="var(--brand-blue)" stroke-width="1.3"/>
        </svg>
        dan@tarnwove.com
      </li>
      <li class="back__contact">
        <svg class="back__icon" viewBox="0 0 16 16" aria-hidden="true">
          <g fill="none" stroke="var(--soft-blue)" stroke-width="1.3">
            <circle cx="8" cy="8" r="6.5"/>
            <ellipse cx="8" cy="8" rx="3" ry="6.5"/>
            <line x1="1.5" y1="8" x2="14.5" y2="8"/>
            <line x1="2.5" y1="4.5" x2="13.5" y2="4.5"/>
            <line x1="2.5" y1="11.5" x2="13.5" y2="11.5"/>
          </g>
        </svg>
        www.tarnwove.com
      </li>
    </ul>
  </section>

</body>
</html>
```